Business card design Needed for new logo / Construction business, home extensions and new builds

We need a business card design using our new logo files which i will attach to this project :)

We are a small construction business specialising in home extensions, new builds and property development. We are very ambitious and would appreciate professional and elegant designs for our new business card.

Very serious about using the services on MakerQuarry and recently acquired our new logo from here :)

Please get involved, i will feedback when i can as i am very busy but can respond daily, thanks

Target Market(s)

People that want to build onto their houses, new building developments or adding too their existing property

Industry/Entity Type

Construction

Contact Information for Business Card

Renwick Tolliver Construction, Lionel Ashby (Managing Director), Tel 07822254961, email - info@renwick-tolliver, www.renwick-tolliver.co.uk

Colors

Designer to choose colors to be used in the design.

Requirements
Must have
• I like a deep grey on the back please. A lot of you have provided black from and back, try mixing things up a little. The black looks cool 😎 Thanks

```html
<!DOCTYPE html>
<html lang="en">
<head>
<meta charset="utf-8">
<title>Renwick Tolliver Construction – Business Card</title>
<link rel="stylesheet" href="https://fonts.googleapis.com/css2?family=Lato:wght@400;700&family=Ubuntu:wght@400;500&display=swap">
<style>
  :root {
    --page-bg: #1b1b1b;
    --card-black: #030303;
    --card-glow: #1e1e1e;
    --back-grey: #2f3031;
    --back-grey-glow: #4a4b4d;
    --gold: #d9a62e;
    --gold-light: #fbd77e;
    --silver: #c9ccd0;
    --text-light: #e6e6e6;
    --band-text: #141414;
  }
  html, body {
    margin: 0;
    width: 1200px;
    height: 1200px;
    overflow: hidden;
    background: var(--page-bg);
  }
  .canvas {
    position: relative;
    width: 1200px;
    height: 1200px;
  }
  .card {
    position: absolute;
    left: 250px;
    width: 700px;
    height: 400px;
    border-radius: 18px;
    overflow: hidden;
    box-shadow: 0 6px 24px rgba(0,0,0,.55);
  }
  .card--front {
    top: 170px;
    background: radial-gradient(ellipse 60% 60% at 50% 45%, var(--card-glow), var(--card-black) 80%);
  }
  .card--back {
    top: 631px;
    background: radial-gradient(ellipse 65% 65% at 50% 45%, var(--back-grey-glow), var(--back-grey) 85%);
  }

  .brand {
    position: absolute;
    left: 0;
    right: 0;
    text-align: center;
    font-family: "Ubuntu", sans-serif;
    font-weight: 500;
    color: var(--silver);
    letter-spacing: 2px;
    text-transform: uppercase;
  }
  .brand__mark {
    display: block;
    margin: 0 auto 14px;
    width: 14px;
    height: 14px;
    background: var(--gold);
  }
  .card--front .brand { top: 88px; font-size: 27px; line-height: 1.25; }
  .card--back .brand  { top: 120px; font-size: 36px; line-height: 1.25; }
  .card--back .brand__mark { width: 20px; height: 20px; margin-bottom: 20px; }

  .contact-row {
    position: absolute;
    top: 268px;
    left: 0;
    width: 700px;
    height: 50px;
  }
  .person {
    position: absolute;
    right: 389px;
    top: 0;
    text-align: right;
    font-family: "Ubuntu", sans-serif;
  }
  .person__name {
    font-size: 27px;
    font-weight: 500;
    color: var(--gold);
    line-height: 30px;
  }
  .person__role {
    font-size: 18px;
    color: var(--text-light);
    line-height: 26px;
  }
  .divider {
    position: absolute;
    left: 334px;
    top: 6px;
    width: 2px;
    height: 42px;
    background: var(--gold);
  }
  .details {
    position: absolute;
    left: 355px;
    top: 0;
    font-family: "Ubuntu", sans-serif;
    color: var(--text-light);
  }
  .details__item {
    display: flex;
    align-items: center;
    gap: 12px;
  }
  .details__item--phone { font-size: 20px; height: 30px; }
  .details__item--mail  { font-size: 16px; height: 26px; }
  .details__icon { width: 16px; height: 16px; flex: none; }

  .band {
    position: absolute;
    left: 0;
    bottom: 0;
    width: 700px;
    height: 38px;
  }
  .band__art { position: absolute; inset: 0; }
  .band__url {
    position: absolute;
    left: 0;
    width: 646px;
    top: 0;
    height: 38px;
    line-height: 38px;
    text-align: center;
    font-family: "Lato", sans-serif;
    font-size: 17px;
    letter-spacing: 2.6px;
    color: var(--band-text);
  }
  .band__url strong { font-weight: 700; }
</style>
</head>
<body>
<main class="canvas">

  <section class="card card--front" aria-label="Card front">
    <div class="brand">
      <span class="brand__mark"></span>
      Renwick Tolliver<br>Construction
    </div>

    <div class="contact-row">
      <div class="person">
        <div class="person__name">Lionel Ashby</div>
        <div class="person__role">Managing Director</div>
      </div>
      <div class="divider"></div>
      <div class="details">
        <div class="details__item details__item--phone">
          <svg class="details__icon" viewBox="0 0 24 24"><path fill="#d9a62e" d="M6.6 10.8a15 15 0 0 0 6.6 6.6l2.2-2.2a1 1 0 0 1 1-.25 11.4 11.4 0 0 0 3.6.57 1 1 0 0 1 1 1V20a1 1 0 0 1-1 1A17 17 0 0 1 3 4a1 1 0 0 1 1-1h3.5a1 1 0 0 1 1 1c0 1.250.2 2.450.57 3.570a1 1 0 0 1-.25 1z"/></svg>
          <span>07822254961</span>
        </div>
        <div class="details__item details__item--mail">
          <svg class="details__icon" viewBox="0 0 24 24"><rect x="2" y="5" width="20" height="14" fill="#d9a62e"/><path d="M2 5l10 8 10-8M2 19l7-7M22 19l-7-7" stroke="#050505" stroke-width="1.6" fill="none"/></svg>
          <span>info@renwick-tolliver.co.uk</span>
        </div>
      </div>
    </div>

    <div class="band">
      <svg class="band__art" viewBox="0 0 700 38" preserveAspectRatio="none">
        <defs>
          <linearGradient id="goldBand" x1="0" x2="1">
            <stop offset="0" stop-color="#c48a1c"/>
            <stop offset=".5" stop-color="#fbd77e"/>
            <stop offset="1" stop-color="#c48a1c"/>
          </linearGradient>
          <linearGradient id="silverTail" x1="0" x2="1">
            <stop offset="0" stop-color="#8e949b"/>
            <stop offset="1" stop-color="#eceef0"/>
          </linearGradient>
        </defs>
        <polygon points="0,0 586,0 617,38 0,38" fill="url(#goldBand)"/>
        <polygon points="586,0 592,0 623,38 617,38" fill="#fbe2a0"/>
        <polygon points="592,0 606,0 637,38 623,38" fill="#000"/>
        <polygon points="606,0 700,0 700,38 637,38" fill="url(#silverTail)"/>
      </svg>
      <div class="band__url">WWW.<strong>RENWICK-TOLLIVER</strong>.CO.UK</div>
    </div>
  </section>

  <section class="card card--back" aria-label="Card back">
    <div class="brand">
      <span class="brand__mark"></span>
      Renwick Tolliver<br>Construction
    </div>

    <div class="band">
      <svg class="band__art" viewBox="0 0 700 38" preserveAspectRatio="none">
        <defs>
          <linearGradient id="silverBand" x1="0" x2="1">
            <stop offset="0" stop-color="#c9ccd0"/>
            <stop offset=".5" stop-color="#e4e6e8"/>
            <stop offset="1" stop-color="#8e949b"/>
          </linearGradient>
          <linearGradient id="goldTail" x1="0" x2="1">
            <stop offset="0" stop-color="#c48a1c"/>
            <stop offset="1" stop-color="#fbd77e"/>
          </linearGradient>
        </defs>
        <polygon points="0,0 586,0 617,38 0,38" fill="url(#silverBand)"/>
        <polygon points="586,0 592,0 623,38 617,38" fill="#f2f3f4"/>
        <polygon points="592,0 606,0 637,38 623,38" fill="#000"/>
        <polygon points="606,0 700,0 700,38 637,38" fill="url(#goldTail)"/>
      </svg>
      <div class="band__url">WWW.<strong>RENWICK-TOLLIVER</strong>.CO.UK</div>
    </div>
  </section>

</main>
</body>
</html>
```